Business Card Design

Business Card for professional consulting firm working with large financial institutions.

Target Market(s)

Executive buyers

Industry/Entity Type

Banking

Contact Information for Business Card

Mild creativity wanted. Not boring, but do elaborate artwork.

Font styles to use
Serif
Sans Serif

Colors

Designer to choose colors to be used in the design.

Requirements
Must have
• Standard business card features - company name, individual name, telephone, website, email, locations.
Nice to have
• Two colors
Should not have
• too many colors, fancy printing, cartoons.

```html
<!DOCTYPE html>
<html lang="en">
<head>
<meta charset="utf-8">
<title>Veldt Partners – Business Card</title>
<link rel="stylesheet" href="https://fonts.googleapis.com/css2?family=Roboto:wght@400&family=Roboto+Slab:wght@400;700&display=swap">
<style>
  :root {
    --backdrop: #d6d6d6;
    --card-white: #f7f7f7;
    --card-black: #1b1b1b;
    --ink: #111111;
    --ink-soft: #4a4a4a;
    --logo-grey: #3a3a3a;
    --paper-white: #ffffff;
  }
  * { margin: 0; padding: 0; box-sizing: border-box; }
  html, body {
    width: 1200px; height: 960px; overflow: hidden;
    background: var(--backdrop);
  }
  .canvas { position: relative; width: 1200px; height: 960px; }

  .card { position: absolute; width: 600px; height: 344px; }
  .card-front { left: 315px; top: 113px; background: var(--card-white); }
  .card-back  { left: 311px; top: 472px; height: 343px; background: var(--card-black);
                display: flex; align-items: center; justify-content: center; }

  .name-band { position: absolute; left: 0; top: 53px; }

  .holder { position: absolute; left: 48px; top: 66px; color: var(--paper-white);
            font-family: "Roboto Slab", Georgia, serif; }
  .holder-name { font-size: 20px; font-weight: 700; letter-spacing: 0.5px; line-height: 1; }
  .holder-title { font-size: 14px; font-weight: 400; margin-top: 6px; margin-left: -2px; letter-spacing: 0.3px; }

  .brand-name { position: absolute; left: 372px; top: 72px; white-space: nowrap;
                font-family: "Roboto Slab", Georgia, serif; font-weight: 400;
                font-size: 26px; line-height: 1; color: var(--logo-grey); }

  .details { position: absolute; left: 48px; top: 198px;
             font-family: "Roboto", Arial, sans-serif; font-size: 14.5px;
             color: var(--ink-soft); line-height: 19px; }
  .address { margin-bottom: 9px; }
  .contact-list { list-style: none; }
  .contact-list li { display: flex; align-items: center; gap: 8px; }
  .contact-list svg { width: 13px; height: 13px; fill: var(--ink); flex: none; }

  .back-name { font-family: "Roboto Slab", Georgia, serif; font-weight: 400;
               font-size: 96px; line-height: 1; color: var(--paper-white); }
</style>
</head>
<body>
<main class="canvas">
  <section class="card card-front" aria-label="Business card front">
    <svg class="name-band" width="380" height="74" viewBox="0 0 380 74" aria-hidden="true">
      <path d="M0 0 H370 Q330 20 315 74 H0 Z" fill="var(--ink)"/>
    </svg>
    <div class="holder">
      <p class="holder-name">DANIEL HARPER</p>
      <p class="holder-title">CEO/FOUNDER</p>
    </div>
    <p class="brand-name">veldtpartners</p>

    <div class="details">
      <p class="address">214 Cedar Hollow Road<br>Juneau, Alaska 99801</p>
      <ul class="contact-list">
        <li>
          <svg viewBox="0 0 16 16" aria-hidden="true"><path d="M3.6 1 6 3.8 4.6 5.6c.9 2.2 3.6 4.9 5.8 5.8l1.8-1.4L15 12.4 13.6 15C7 14.6 1.4 9 1 2.4Z"/></svg>
          <span>555 218 4470</span>
        </li>
        <li>
          <svg viewBox="0 0 16 16" aria-hidden="true"><path d="M1 3h14v1.2L8 8.6 1 4.2Z M1 5.8l7 4.4 7-4.4V13H1Z"/></svg>
          <span>info@veldtpartners.com</span>
        </li>
        <li>
          <svg viewBox="0 0 16 16" aria-hidden="true"><circle cx="8" cy="8" r="7"/><path d="M5 4c1 1 0 2 1 3s2 0 2 2-1 2 0 4M10 3c0 1 1 2 2 2" stroke="var(--card-white)" stroke-width="1.2" fill="none"/></svg>
          <span>www.veldtpartners.com</span>
        </li>
      </ul>
    </div>
  </section>

  <section class="card card-back" aria-label="Business card back">
    <p class="back-name">veldt</p>
  </section>
</main>
</body>
</html>
```